3 Business Card designs for a company with multiple services

We are a company that has 3 main services:

1) Security - CCTV & Alarm Sepcialists
2) Broadcast - Broadcast Sales and Technical Services
3) Distribution - Quality Products, Quality Service

The broadcast service is for Video Broadcast.

I will include our logos for each service.

I would like to also create a business card design for 7QR in general (see main logo).

Each card will be two-sided. On the front I would think it would include Logo, Name, Posistion and Mobile (and possibly email). And possibly our main number (which may be something like 1800 639 415)

On the back it MUST include a "lined" section to be able to write short quotes / prices.

Then include more details like Phone: 1800 639 415 Fax: 1800 639 417 Postal: PO Box 917, Tallowfield, QLD Australia 4287 Website: www.7qr.com.au

We would like a fresh, inovative card design with that "wow check this out" feel about it.

Look forward to seeing what you can do! :)

Corin

• Quote section on the back!
Editable files.

```html
<!DOCTYPE html>
<html lang="en">
<head>
<meta charset="utf-8">
<title>7QR Business Card – Front and Back</title>
<link href="https://fonts.googleapis.com/css2?family=PT+Sans:wght@400;700&display=swap" rel="stylesheet">
<style>
  :root {
    --stage: #1b1a1a;
    --card-front: #d0d1d3;
    --card-back: #f0f0f1;
    --ink: #111111;
    --ink-soft: #444444;
    --mark-square: #2a2a2b;
    --rule: #a9a9ab;
  }
  * { margin: 0; padding: 0; box-sizing: border-box; }
  html, body {
    width: 1200px;
    height: 934px;
    overflow: hidden;
    background: var(--stage);
    font-family: "PT Sans", sans-serif;
  }
  .card {
    position: absolute;
    left: 251px;
    width: 698px;
    height: 393px;
    border-radius: 12px;
    box-shadow: 0 6px 14px rgba(0,0,0,0.6);
  }
  .card--front { top: 42px; background: var(--card-front); }
  .card--back { top: 497px; background: var(--card-back); }

  .brand {
    position: absolute;
    left: 43px;
    display: flex;
    flex-direction: column;
    justify-content: center;
  }
  .brand__name {
    display: flex;
    align-items: center;
    gap: 0.3em;
    color: var(--ink);
    font-weight: 700;
    line-height: 1;
  }
  .brand__square {
    width: 0.75em;
    height: 0.75em;
    background: var(--mark-square);
  }
  .brand__services {
    color: var(--ink-soft);
    font-weight: 400;
    white-space: nowrap;
  }

  .card--front .brand { top: 41px; width: 613px; height: 142px; align-items: center; }
  .card--front .brand__name { font-size: 64px; }
  .card--front .brand__services { margin-top: 14px; font-size: 20px; }

  .card--back .brand { top: 44px; width: 347px; height: 80px; }
  .card--back .brand__name { font-size: 40px; }
  .card--back .brand__services { margin-top: 8px; font-size: 15px; }

  .contact-front {
    position: absolute;
    top: 238px;
    left: 0;
    width: 100%;
    text-align: center;
    color: var(--ink-soft);
    font-size: 16px;
    line-height: 22px;
  }
  .contact-front__name { color: var(--ink); font-weight: 700; font-size: 21px; line-height: 26px; }
  .contact-front__role { margin-bottom: 20px; }

  .contact-back {
    position: absolute;
    top: 44px;
    left: 414px;
    color: var(--ink-soft);
    font-size: 16px;
    line-height: 22px;
    font-style: normal;
  }

  .quote-lines {
    position: absolute;
    top: 178px;
    left: 43px;
    width: 618px;
    list-style: none;
  }
  .quote-lines li {
    height: 43.5px;
    border-top: 2px solid var(--rule);
  }
</style>
</head>
<body>
  <section class="card card--front" aria-label="Business card front">
    <div class="brand">
      <p class="brand__name"><span class="brand__square"></span>7QR</p>
      <p class="brand__services">Security, Broadcast and Distribution</p>
    </div>
    <div class="contact-front">
      <p class="contact-front__name">Corin Hale</p>
      <p class="contact-front__role">Director</p>
      <p>M. 1800 639 417</p>
      <p>corin@7qr.com.au</p>
    </div>
  </section>

  <section class="card card--back" aria-label="Business card back">
    <div class="brand">
      <p class="brand__name"><span class="brand__square"></span>7QR</p>
      <p class="brand__services">Security, Broadcast and Distribution</p>
    </div>
    <address class="contact-back">
      PO Box 917, Tallowfield,<br>
      QLD Australia 4287<br>
      P. 1800 639 415&nbsp; F. 1800 639 417<br>
      www.7qr.com.au
    </address>
    <ul class="quote-lines" aria-label="Lined quote section">
      <li></li><li></li><li></li><li></li><li></li>
    </ul>
  </section>
</body>
</html>
```